New Web Design needed for our Consulting Business

We have an existing Website that we want a fresh new design for.
www.quorniflow.com.au
Our business is Norvane Tabulo Consulting and we provide services to develop custom spreadsheets to improve business efficiency. We also offer a range of spreadsheets and templates for sale via our website.
Design Deliverables
- Provide a framework for the sites Home Page and each of the key Sub Sections on the site.
- The design deliverable should list the key functions on each framework page so that a developer can interpret those functions for implementation
- The design must include a mobile version for phones and tablet devices or show how the site will appear on those devices.
- We want to project a fresh and professional image with the latest design options for websites
- The existing Logo should be retained and the new design built from that.
What I expect to receive at the end of the Design Project
1) A complete set of design files that can be used by a web developer to construct our new website
2) All image files and colour schemes documented for each page
3) As part of the design the implementation of the functionality listed below is to be clearly documented throughout the site design
4) A word document that provides any key notes or instructions for the web developer to follow for the implementation
Key Sections
Home Page
Tabulo Consulting
Tabulo Software
Free Spreadsheet & Templates
Customer Support
- Blog
- FAQs
- Common Problems
Contact Us
Key Functions
The website must support the following key functions and these should be shown in the design
- Contact Us visible through the site. When a visitor submits a Contact Us form it is stored to a database with a ticket number. Emails are then sent via that Ticket number and stored against that contact on the website for review by our support team. Basically a support ticket tracking system.
- To download a free template or spreadsheet the user must register to the site to receive the download. Those registrations to be kept for later use in email marketing campaigns for the site. Once registered a user can return and "Login" to the site to access more free downloads
- A Blog should be implemented to include interesting articles and information about Quorniflow and Tabulo. This should be a standard Blog design and allow others to comment if they choose to.
- Product Purchase, on the site we offer some products for sale. This currently goes to a 3rd party site for processing. We would like to see this integrated to the site so that the purchase is within our site and also the registration and licence verification. For the design this just needs to show how a Product Purchase would look.
- Site Search will be implemented to provide a site wide search and return results from our site first and then other google results.
- SPAM and Security is a high priority for the site. So the latest protection must be implemented to ensure that the site does not suffer any breach.

```html
<!DOCTYPE html>
<html lang="en">
<head>
<meta charset="utf-8">
<title>About Quorniflow</title>
<link rel="stylesheet" href="https://fonts.googleapis.com/css2?family=Ubuntu:wght@300;400;500;700&display=swap">
<style>
:root{
  --ink:#1d1d1d;
  --muted:#3a3a3a;
  --sky:#6f9bd6;
  --link:#4f7cc4;
  --nav-top:#7aa0de;
  --nav-bot:#3d66b8;
  --nav-line:#555;
  --side-bg:#f1f1f1;
  --side-head-top:#6a6a6a;
  --side-head-bot:#4b4b4b;
  --rule:#9a9a9a;
  --card-bg:#dcdcdc;
  --footer-bg:#f0f0f0;
  --bar-bg:#dedede;
  --icon:#6c9ed9;
  --brand:#3d66b8;
}
*{box-sizing:border-box;margin:0;padding:0}
html,body{width:1200px;height:1200px;overflow:hidden;background:#fff}
body{font-family:"Ubuntu",sans-serif;color:var(--ink);position:relative}
.abs{position:absolute}

/* header */
.brand{left:105px;top:40px;display:flex;align-items:center;gap:12px}
.brand-dot{width:62px;height:62px;border-radius:50%;background:var(--brand)}
.brand-name{font-size:34px;font-weight:500;color:var(--brand)}
.utility{right:61px;top:27px;font-size:17px;color:#111}
.utility span{margin:0 4px}
.social{top:58px;left:929px;display:flex;gap:8px}
.social i{display:block;width:36px;height:36px;border-radius:50%;background:#1e6fb4}
.phone{left:674px;top:110px;font-size:22px;color:#111;letter-spacing:.5px}
.search{left:879px;top:103px;width:221px;height:40px;border:2px solid #cfcfcf;border-radius:7px;background:#fafafa;display:flex}
.search-field{flex:1;padding:9px 12px;font-size:17px;color:#9a9a9a}
.search-btn{width:40px;border-left:2px solid #cfcfcf;display:flex;align-items:center;justify-content:center}

/* nav */
.nav{left:0;top:179px;width:1200px;height:52px;background:linear-gradient(var(--nav-top),var(--nav-bot));border-top:3px solid var(--nav-line);display:flex;color:#fff;font-size:19px;font-weight:500}
.nav a{color:#fff;text-decoration:none;display:flex;align-items:center;justify-content:center;border-right:1px solid rgba(255,255,255,.35);height:100%}

/* main */
.page-title{left:29px;top:248px;font-size:33px;font-weight:300;color:var(--sky)}
.intro{left:29px;top:305px;width:762px;font-size:18.5px;line-height:22.5px;color:#111;letter-spacing:.6px;hyphens:auto;-webkit-hyphens:auto}
.team-lead{left:29px;top:419px;font-size:20px;font-weight:300;font-style:italic;color:var(--sky);letter-spacing:.3px}
.bio{left:29px;top:466px;font-size:18.5px;line-height:22.5px;list-style:none;letter-spacing:.4px}

.card{top:611px;width:362px;height:255px;border:1px solid #bdbdbd;background:linear-gradient(#fff 55%,var(--card-bg))}
.card-img{position:absolute;left:4px;top:4px;width:352px;height:118px;box-shadow:0 6px 6px -3px rgba(0,0,0,.5)}
.card-title{position:absolute;left:17px;top:128px;font-size:24px;font-weight:500;color:var(--link)}
.card-text{position:absolute;left:19px;top:158px;width:322px;font-size:18px;line-height:22.5px;color:#222;letter-spacing:.3px;hyphens:auto;-webkit-hyphens:auto}
.card-more{position:absolute;right:12px;bottom:8px;font-size:14px;font-weight:500;color:var(--link);display:flex;align-items:center;gap:4px}

/* sidebar */
.sidebar{left:824px;top:246px;width:376px;height:648px;background:linear-gradient(90deg,#e6e6e6,#fff 18%)}
.side-head{position:absolute;left:0;width:376px;height:33px;background:linear-gradient(var(--side-head-top),var(--side-head-bot));border-top:4px solid #8fb2e3;color:#fff;font-size:19px;padding:3px 28px}
.product{position:absolute;left:32px;top:70px;width:155px;height:103px;border:1px solid #ccc;border-radius:4px;box-shadow:0 6px 8px rgba(0,0,0,.18)}
.product-info{position:absolute;left:202px;top:68px;width:160px}
.product-name{font-size:14px;font-weight:700;font-style:italic;color:var(--link)}
.product-price{font-size:11px;color:#555}
.product-price b{color:#e2691e;font-weight:400}
.product-desc{font-size:12px;line-height:15px;margin-top:6px;color:#111}
.pill{display:inline-block;font-size:10px;font-weight:700;color:#fff;padding:1px 6px;border-radius:8px;margin-top:3px}
.pill.trial{background:#2d6fc4}
.pill.buy{background:#222}
.side-menu{position:absolute;left:32px;top:264px;width:304px;list-style:none;border-top:1px solid var(--rule)}
.side-menu li{height:34px;border-bottom:1px solid var(--rule);border-right:6px solid #6a6a6a;font-size:18.5px;padding:5px 0 0 0;color:#111}
.side-menu li.active{border-right-color:#8fb2e3}
.trial-cta{position:absolute;left:32px;top:558px;width:304px;height:66px;border-radius:9px;background:linear-gradient(#6f9ae0,#3d66b8);overflow:hidden}
.trial-cta-text{position:absolute;left:143px;top:3px;color:#fff;font-size:20px;line-height:19px}
.trial-cta-text b{font-weight:700}

/* footer */
.footer{left:0;top:894px;width:1200px;height:243px;background:var(--footer-bg);border-top:2px dashed #aaa}
.feature-box{position:absolute;top:41px;width:123px;height:116px;border:3px solid #8d8d8d;background:#f7f7f7}
.feature-text{position:absolute;font-size:20px;line-height:18px;color:#333}
.feature-text b{font-weight:700}
.big-stat{font-size:46px;font-weight:700;color:var(--icon);line-height:44px}
.subscribe{position:absolute;left:32px;top:180px;display:flex;gap:5px}
.subscribe-field{width:250px;height:36px;border:2px solid #c4c4c4;background:#fff;font-size:16px;color:#888;padding:8px 16px;letter-spacing:.5px}
.subscribe-btn{width:46px;height:36px;background:#8a8a8a;display:flex;align-items:center;justify-content:center}
.bottom-bar{left:0;top:1137px;width:1200px;height:63px;background:var(--bar-bg);text-align:center;font-size:15.5px;color:#111}
.bottom-links{padding-top:10px;word-spacing:2px}
.bottom-links span{margin:0 4px}
.copyright{font-size:16.5px;margin-top:4px}
</style>
</head>
<body>

<header>
  <div class="abs brand"><span class="brand-dot"></span><span class="brand-name">Quorniflow</span></div>
  <div class="abs utility">Login <span>|</span> Newsletter <span>|</span> Blog <span>|</span> Members</div>
  <div class="abs social" aria-label="Social links"><i></i><i></i><i></i></div>
  <div class="abs phone">+61 (7) 5550 1274</div>
  <div class="abs search">
    <div class="search-field">Search..</div>
    <div class="search-btn"><svg width="18" height="18" viewBox="0 0 18 18"><circle cx="10" cy="7" r="5" fill="none" stroke="#666" stroke-width="2"/><line x1="6.5" y1="10.5" x2="2" y2="15" stroke="#666" stroke-width="2.4"/></svg></div>
  </div>
</header>

<nav class="abs nav">
  <a style="width:129px">Home</a>
  <a style="width:199px">Tabulo Consulting</a>
  <a style="width:176px">Tabulo Software</a>
  <a style="width:311px">Free Spreadsheet &amp; Templates</a>
  <a style="width:211px">Customer Support</a>
  <a style="width:174px;border-right:0">Contact Us</a>
</nav>

<main>
  <h1 class="abs page-title">About Quorniflow</h1>
  <p class="abs intro">Quorniflow is a technology solutions company focused on delivering process im&shy;provements through the use of Norvane Office® automation. The key to our success is a team of professionals committed to delivering the best possible solution at a rea&shy;sonable cost for our clients.</p>
  <p class="abs team-lead">Meet the Quorniflow team...</p>
  <ul class="abs bio">
    <li>•Development Manager - Darren Holloway</li>
    <li>•B.A. Computer Science &amp; Economic History (CTU)</li>
    <li>•Graduate Diploma Applied Finance &amp; Investment (FIA)</li>
    <li>•PROVENA2 and MPX Practitioner Accreditiation</li>
  </ul>

  <article class="abs card" style="left:32px">
    <div class="card-img" role="img" aria-label="Photo of a consultant in a suit beside the word consulting" style="background:linear-gradient(90deg,#1a2a4a,#2f5fa8 60%,#3f8fd8)"></div>
    <h2 class="card-title">Why Choose Us?</h2>
    <p class="card-text">lorem ipsum dolor sit amet, consecte&shy;tur adipisicing elit, sed do eiusmod tempor incididunt ut labore</p>
    <div class="card-more">See our reasons <svg width="12" height="12"><circle cx="6" cy="6" r="5" fill="none" stroke="#4f7cc4"/><path d="M5 3.5 7.5 6 5 8.5" fill="none" stroke="#4f7cc4"/></svg></div>
  </article>
  <article class="abs card" style="left:436px">
    <div class="card-img" role="img" aria-label="Photo of hands reviewing printed charts on a desk" style="background:linear-gradient(120deg,#e9ebee,#c9cdd3 60%,#9ea4ab)"></div>
    <h2 class="card-title">Meet our tem</h2>
    <p class="card-text">lorem ipsum dolor sit amet, consecte&shy;tur adipisicing elit, sed do eiusmod tempor incididunt ut labore</p>
    <div class="card-more">The team <svg width="12" height="12"><circle cx="6" cy="6" r="5" fill="none" stroke="#4f7cc4"/><path d="M5 3.5 7.5 6 5 8.5" fill="none" stroke="#4f7cc4"/></svg></div>
  </article>
</main>

<aside class="abs sidebar">
  <div class="side-head" style="top:0">Top selling software</div>
  <div class="product" role="img" aria-label="Tablet showing a green bar chart" style="background:linear-gradient(135deg,#f4f4f4,#c8c8c8 55%,#6aa64a)"></div>
  <div class="product-info">
    <div class="product-name">Task Ledger</div>
    <div class="product-price">Price: <b>$150</b></div>
    <div class="product-desc">Project you TBS projects from unauthorised copying and re-use.</div>
    <span class="pill trial">Free Trial</span> <span class="pill buy">Purchase</span>
  </div>
  <div class="side-head" style="top:220px">Tabulo Consulting</div>
  <ul class="side-menu">
    <li class="active">Consulting Overview</li>
    <li>Macro Programming</li>
    <li>Spreadsheet Development</li>
    <li>Tabulo Dashboard Reporting</li>
    <li>Customer Testimonials</li>
    <li>Programming &amp; Consulting Rates</li>
    <li>About Us</li>
    <li>Newsletter</li>
  </ul>
  <div class="trial-cta">
    <svg class="abs" style="left:0;top:0" width="304" height="66"><path d="M0 0H74L110 33 74 66H0L36 33Z" fill="#fff" opacity=".9"/></svg>
    <div class="trial-cta-text">GET YOUR<br><b>FREE TRIAL<br>NOW</b></div>
  </div>
</aside>

<footer class="abs footer">
  <div class="feature-box" style="left:111px">
    <svg width="117" height="110"><rect x="20" y="79" width="20" height="28" fill="#6c9ed9"/><rect x="47" y="63" width="20" height="44" fill="#6c9ed9"/><rect x="74" y="46" width="20" height="61" fill="#6c9ed9"/></svg>
  </div>
  <div class="feature-text" style="left:296px;top:94px">Faster<br><b>Growing</b></div>
  <div class="feature-box" style="left:437px">
    <svg width="117" height="110"><path d="M14 52 32 40 52 70 104 18 92 78 56 103Z" fill="#6c9ed9"/></svg>
  </div>
  <div class="feature-text" style="left:604px;top:78px">Automating<br>Business<br><b>Guaranteed</b></div>
  <div class="feature-box" style="left:765px">
    <svg width="117" height="110"><path d="M22 18Q58 4 95 18V55Q95 85 58 103 22 85 22 55Z" fill="#6c9ed9"/></svg>
  </div>
  <div class="feature-text" style="left:941px;top:50px;text-align:center"><div class="big-stat">100<span style="font-size:30px">%</span></div>Web Security<br><b>No risk at all</b></div>
  <div class="subscribe">
    <div class="subscribe-field">Enter your email address:</div>
    <div class="subscribe-btn"><svg width="26" height="22"><path d="M4 2 16 11 4 20" fill="none" stroke="#fff" stroke-width="5"/></svg></div>
  </div>
</footer>

<div class="abs bottom-bar">
  <div class="bottom-links"><span>Home</span><span>Tabulo Consulting</span><span>Tabulo Software</span><span>Free Spreadsheet &amp; Templates</span><span>Customer Support</span><span>Contact Us</span></div>
  <div class="copyright">Copyright 2013 @ Quorniflow. All rights reserved</div>
</div>

</body>
</html>
```